Dorvik Electric Ltd

Looking for a single page website and Facebook page design. I am an electrical contractor based on Vancouver Island. I do service, custom homes, residential and commercial installations. My company just started out, so I don't have any pictures of installs yet. I have 25 years experience. I would like the colors to be my logo colors black and I have a black Brandt Halvard that will be my vehicle which I will have a wrap for.
Updates

I just posted the contest today, not sure why the deadline is the same day.

Industry/Entity Type

Electrician

Requirements
Must have
• Services provided, About me section, quote section,
Nice to have
• I am not quite sure yet, I need to see some designs first .

```html
<!DOCTYPE html>
<html lang="en">
<head>
<meta charset="utf-8">
<title>Dorvik Electric Ltd</title>
<link href="https://fonts.googleapis.com/css2?family=Josefin+Sans:wght@600;700&family=Sarabun:wght@400;600&display=swap" rel="stylesheet">
<style>
:root{
  --yellow:#f4b400;
  --dark:#1b1b1b;
  --darker:#111111;
  --text:#222222;
  --white:#ffffff;
  --field:#ffffff;
}
*{box-sizing:border-box;margin:0;padding:0}
html,body{width:1200px;height:3748px;overflow:hidden}
body{position:relative;background:var(--white);font-family:"Sarabun",sans-serif;color:var(--text)}
.abs{position:absolute}
.heading{font-family:"Josefin Sans",sans-serif;font-weight:700;letter-spacing:2px;text-transform:uppercase}
.btn{position:absolute;display:flex;align-items:center;justify-content:center;border-radius:4px;font-family:"Josefin Sans",sans-serif;font-weight:700;letter-spacing:1px;font-size:15px}
.btn-yellow{background:var(--yellow);color:var(--white)}
.btn-white{background:var(--white);color:var(--yellow)}

/* hero */
.hero{position:absolute;left:0;top:0;width:1200px;height:1204px;background:
  repeating-linear-gradient(120deg,rgba(255,255,255,.025) 0 2px,transparent 2px 14px),var(--dark)}
.hero-backdrop{position:absolute;left:0;top:0;width:1200px;height:700px;
  background:linear-gradient(90deg,#3c3c3c 0%,#4a4a4a 35%,#3a3a3a 60%,#2e2e2e 100%);
  clip-path:polygon(0 0,100% 0,100% 620px,0 672px)}
.hero-worker{position:absolute;left:470px;top:0;width:730px;height:900px;
  background:
    radial-gradient(ellipse 120px 80px at 420px 120px,#e6e6e6 0%,#cfcfcf 60%,transparent 100%),
    radial-gradient(ellipse 130px 150px at 430px 270px,#8f8a86 0%,#6e6a67 70%,transparent 100%),
    radial-gradient(ellipse 260px 300px at 430px 560px,#7a7a7a 0%,#5c5c5c 55%,transparent 100%),
    radial-gradient(ellipse 170px 220px at 100px 330px,#b8b8b8 0%,#8a8a8a 50%,transparent 100%),
    linear-gradient(90deg,rgba(70,70,70,0) 0%,#555 20%,#5a5a5a 70%,#2a2a2a 100%);
  clip-path:polygon(0 0,100% 0,100% 620px,72% 750px,30% 760px,0 680px)}
.brand{position:absolute;left:113px;top:40px;display:flex;align-items:center;gap:10px;color:var(--white);font-family:"Josefin Sans",sans-serif;font-weight:700;font-size:15px;letter-spacing:.5px}
.brand-dot{width:22px;height:22px;border-radius:50%;background:var(--yellow)}
.nav a{position:absolute;top:57px;color:var(--white);font-size:15px;text-decoration:none}
.nav a.active{color:var(--yellow)}
.phone-dot{position:absolute;left:901px;top:42px;width:44px;height:44px;border-radius:50%;background:var(--yellow);display:flex;align-items:center;justify-content:center}
.phone-num{position:absolute;left:958px;top:52px;color:var(--white);font-weight:600;font-size:19px}
.welcome{left:112px;top:218px;color:var(--yellow);font-size:27px;letter-spacing:3px}
.hero-title{left:106px;top:262px;color:var(--white);font-size:64px;line-height:65px;letter-spacing:5px}
.hero-text{left:112px;top:398px;width:430px;color:#eee;font-size:15.5px;line-height:26px}
.diamond{position:absolute;left:126px;top:572px;width:40px;height:40px;border:1.5px solid var(--white);transform:rotate(45deg)}
.down-line{position:absolute;left:145px;top:620px;width:1.5px;height:163px;background:#ccc}

.eyebrow{left:113px;top:864px;color:var(--yellow);font-size:15px;letter-spacing:1.5px;display:flex;align-items:center;gap:8px}
.eyebrow::before{content:"";width:22px;height:2px;background:var(--yellow)}
.about-title{left:109px;top:896px;color:var(--white);font-size:43px;line-height:44px;letter-spacing:3px}
.about-text{left:460px;top:930px;width:630px;color:#e6e6e6;font-size:15px;line-height:25.7px}
.photo{position:absolute}

/* services */
.band{position:absolute;left:0;top:1204px;width:1200px;height:1049px}
.areas{left:0;width:1200px;top:1636px;text-align:center;color:var(--yellow);font-size:14px;letter-spacing:1.5px}
.areas-rule{position:absolute;left:585px;top:1656px;width:30px;height:2px;background:var(--yellow)}
.services-title{left:0;width:1200px;top:1668px;text-align:center;color:var(--text);font-size:38px;letter-spacing:4px}
.panel{position:absolute;top:1748px;height:403px;overflow:hidden}
.panel-cap{position:absolute;bottom:36px;left:0;right:0;text-align:center;color:var(--white);font-family:"Josefin Sans",sans-serif;font-weight:700;letter-spacing:2px;font-size:21px;line-height:26px;text-transform:uppercase}
.panel-body{position:absolute;top:132px;left:30px;right:42px;text-align:center;color:var(--white)}
.panel-body h3{font-size:21px;line-height:26px;margin-bottom:12px}
.panel-body p{font-size:14.5px;line-height:25.6px;color:#fff8e0;font-weight:400}

/* testimonials */
.testimonials{position:absolute;left:0;top:2253px;width:1200px;height:493px;background:linear-gradient(110deg,#2a2a2a 0%,#1d1d1d 50%,#262626 100%)}
.t-title{left:0;width:1200px;top:2312px;text-align:center;color:var(--white);font-size:32px;letter-spacing:3px}
.t-text{left:186px;top:2492px;width:828px;text-align:center;color:#f0f0f0;font-size:15.5px;line-height:30.7px}
.t-name{left:0;width:1200px;top:2628px;text-align:center;color:var(--yellow);font-family:"Josefin Sans",sans-serif;font-weight:700;letter-spacing:1.5px;font-size:19px}
.t-role{left:0;width:1200px;top:2660px;text-align:center;color:#ddd;font-size:14px}
.arrow-box{position:absolute;top:2510px;width:32px;height:32px;display:flex;align-items:center;justify-content:center}

/* contact */
.c-title{left:0;width:1200px;top:2808px;text-align:center;color:var(--text);font-size:38px;letter-spacing:4px}
.quote-title{left:158px;top:2906px;font-size:27px;letter-spacing:3px;color:var(--text)}
.info-label{position:absolute;left:190px;font-weight:600;font-size:15.5px;letter-spacing:1px;color:var(--text)}
.info-line{position:absolute;left:191px;font-size:15.5px;line-height:26px;color:var(--text)}
.info-icon{position:absolute;left:160px}
.field{position:absolute;left:550px;width:490px;height:56px;background:var(--field);box-shadow:0 2px 10px rgba(0,0,0,.09);border-radius:2px;padding:0 30px;display:flex;align-items:center;color:#888;font-size:15px}

/* footer */
.footer{position:absolute;left:0;top:3305px;width:1200px;height:443px;background:var(--darker);clip-path:polygon(0 58px,100% 0,100% 100%,0 100%)}
.f-mark{position:absolute;left:196px;top:3420px;width:80px;height:80px;border-radius:50%;border:5px solid var(--yellow)}
.f-name{left:112px;top:3535px;color:var(--white);font-family:"Josefin Sans",sans-serif;font-weight:700;font-size:23px;letter-spacing:.5px}
.social{position:absolute;top:3587px;width:28px;height:28px;border-radius:50%;background:#3a3a3a}
.f-head{position:absolute;top:3410px;color:var(--white);font-size:21px;letter-spacing:2px}
.f-list{position:absolute;top:3451px;list-style:none;color:#e8e8e8;font-size:15px;line-height:30px}
.f-list li::before{content:"«";margin-right:9px}
.news-input{position:absolute;left:810px;top:3459px;width:277px;height:40px;border:1px solid #777;border-radius:4px;color:#999;font-size:15px;display:flex;align-items:center;padding-left:16px}
.f-rule{position:absolute;left:112px;top:3661px;width:976px;height:1px;background:#333}
.copy{left:0;width:1200px;top:3692px;text-align:center;color:#eee;font-size:15px}
</style>
</head>
<body>

<section class="hero">
  <div class="hero-backdrop" role="img" aria-label="Electrical panel with wiring in a grey workshop"></div>
  <div class="hero-worker" role="img" aria-label="Smiling electrician in white hard hat, safety glasses and work gloves reaching into an electrical panel"></div>
</section>

<header>
  <div class="brand"><span class="brand-dot"></span>DORVIK ELECTRIC Ltd</div>
  <nav class="nav">
    <a class="active" style="left:367px">Home</a>
    <a style="left:445px">About Us</a>
    <a style="left:545px">Our Services</a>
    <a style="left:669px">Our Blog</a>
    <a style="left:765px">Contact Us</a>
  </nav>
  <div class="phone-dot">
    <svg width="18" height="18" viewBox="0 0 24 24"><path fill="#fff" d="M6.6 10.8a15 15 0 0 0 6.6 6.6l2.2-2.2c.3-.3.7-.4 1-.2 1.1.4 2.3.6 3.6.6.6 0 1 .4 1 1V20c0 .6-.4 1-1 1A17 17 0 0 1 3 4c0-.6.4-1 1-1h3.5c.6 0 1 .4 1 1 0 1.3.2 2.5.6 3.6.1.3 0 .7-.2 1z"/></svg>
  </div>
  <div class="phone-num">044-870 215 364</div>
</header>

<div class="abs heading welcome">Welcome to</div>
<h1 class="abs heading hero-title">Dorvik<br>Electric Ltd</h1>
<p class="abs hero-text">Lorem ipsum dolor sit amet, consectetur adipiscing elit, sed do eiusmod tempor incididunt ut labore et</p>
<div class="btn btn-yellow" style="left:112px;top:471px;width:205px;height:52px">CONTACT US TODAY</div>
<div class="diamond"></div>
<svg class="abs" style="left:139px;top:585px" width="14" height="14" viewBox="0 0 14 14"><path d="M3 5l4 4 4-4" stroke="#fff" stroke-width="1.6" fill="none"/></svg>
<div class="down-line"></div>

<div class="abs heading eyebrow">About Us</div>
<h2 class="abs heading about-title">Dorvik<br>Electric Ltd</h2>
<div class="btn btn-yellow" style="left:110px;top:1002px;width:159px;height:51px">LEARN MORE</div>
<p class="abs about-text">Lorem ipsum dolor sit amet, consectetur adipiscing elit, sed do eiusmod tempor incididunt ut labore et dolore magna aliqua. Quis ipsum suspendisse ultrices gravida. Risus commodo viverra maecenas accumsan lacus vel facilisis. Lorem ipsum dolor sit amet, consectetur adipiscing elit, sed do eiusmod tempor incididunt ut labore et dolore magna aliqua. Quis ipsum suspendisse ultrices gravida.</p>

<svg class="band" viewBox="0 0 1200 1049" aria-hidden="true"><polygon points="1171,0 1309,0 815,1049 596,1049" fill="var(--yellow)"/></svg>

<div class="photo" style="left:112px;top:1110px;width:410px;height:342px;background:linear-gradient(180deg,#b9c8d6 0%,#d9dcdf 40%,#2a2a2a 60%,#9a9a9a 100%)" role="img" aria-label="Black Brandt Halvard pickup truck parked in front of a building"></div>
<div class="photo" style="left:541px;top:1164px;width:547px;height:388px;background:linear-gradient(180deg,#e8e4e2 0%,#d8d6d6 45%,#5e6f8a 75%,#9a9893 100%)" role="img" aria-label="Three workers in hard hats reviewing plans in front of a new house"></div>

<div class="abs heading areas">Our Business Areas</div>
<div class="areas-rule"></div>
<h2 class="abs heading services-title">Our Services</h2>

<div class="panel" style="left:0;width:292px;clip-path:polygon(0 0,257px 0,292px 100%,0 100%);background:linear-gradient(160deg,#c58a4e 0%,#8a5a30 55%,#3b2a1e 100%)" role="img" aria-label="Timber frame of a custom home under construction">
  <div class="panel-cap" style="right:20px">Custom Homes</div>
</div>
<div class="panel" style="left:263px;width:338px;clip-path:polygon(0 0,304px 0,338px 100%,35px 100%);background:linear-gradient(160deg,#c9a23a 0%,#e8b100 45%,#f4b400 100%)" role="img" aria-label="Electrician installing wiring in a residential ceiling">
  <div class="panel-body">
    <h3 class="heading">Residential<br>Installations</h3>
    <p>Lorem ipsum dolor sit amet, consectetur adipiscing elit, sed do eiusmod tempor incididunt ut labore et dolore magna aliqua. Quis ipsum suspendisse</p>
  </div>
  <div class="btn btn-white" style="left:90px;top:325px;width:156px;height:48px;font-family:'Sarabun',sans-serif;font-weight:600;font-size:15px">Learn More</div>
</div>
<div class="panel" style="left:573px;width:338px;clip-path:polygon(0 0,304px 0,338px 100%,34px 100%);background:linear-gradient(160deg,#5a5a5a 0%,#8a8a8a 40%,#3c3c3c 100%)" role="img" aria-label="Electrician in hard hat fitting a pendant light">
  <div class="panel-cap" style="left:30px">Commercial<br>Installations</div>
</div>
<div class="panel" style="left:883px;width:317px;clip-path:polygon(0 0,100% 0,100% 100%,34px 100%);background:linear-gradient(160deg,#4a4f55 0%,#7b8087 45%,#33363a 100%)" role="img" aria-label="Hand with screwdriver working on switchgear in an electrical cabinet">
  <div class="panel-cap" style="left:30px">Lorem Ipsum</div>
</div>

<section class="testimonials" role="img" aria-label="Dim photo of a construction worker on a building site"></section>
<h2 class="abs heading t-title">See What Our Clients Say</h2>
<svg class="abs" style="left:540px;top:2362px" width="120" height="110" viewBox="0 0 120 110" aria-hidden="true">
  <circle cx="60" cy="55" r="47" fill="none" stroke="var(--white)" stroke-width="3"/>
  <path d="M60 8 A47 47 0 0 1 86 94" fill="none" stroke="var(--yellow)" stroke-width="5"/>
</svg>
<div class="abs" style="left:564px;top:2381px;width:72px;height:72px;border-radius:50%;background:linear-gradient(160deg,#8fa3b8,#c89b7b)" role="img" aria-label="Client portrait"></div>
<p class="abs t-text">Lorem ipsum dolor sit amet, consectetur adipiscing elit, sed do eiusmod tempor incididunt ut labore et dolore magna aliqua. Ut enim ad minim veniam, quis nostrud exercitation ullamco laboris nisi ut aliquip ex ea commodo consequat. Duis aute irure dolor in reprehenderit in voluptate velit esse cillum dolore eu fugiat nulla pariatur. Excepteur sint occaecat cupidatat non proident, sunt in culpa qui officia deserunt mollit anim id est laborum.</p>
<div class="abs t-name">Marlow Trevane</div>
<div class="abs t-role">Lorem Ipsum</div>
<div class="arrow-box" style="left:94px;background:var(--white)">
  <svg width="14" height="14" viewBox="0 0 14 14"><path d="M12 7H2M6 3L2 7l4 4" stroke="var(--yellow)" stroke-width="1.8" fill="none"/></svg>
</div>
<div class="arrow-box" style="left:1072px;background:var(--yellow)">
  <svg width="14" height="14" viewBox="0 0 14 14"><path d="M2 7h10M8 3l4 4-4 4" stroke="#fff" stroke-width="1.8" fill="none"/></svg>
</div>

<h2 class="abs heading c-title">Contact Us</h2>
<h3 class="abs heading quote-title">Get a Quote</h3>

<svg class="info-icon" style="top:2980px" width="14" height="18" viewBox="0 0 14 18"><path d="M7 0a7 7 0 0 0-7 7c0 5 7 11 7 11s7-6 7-11a7 7 0 0 0-7-7zm0 9.5A2.5 2.5 0 1 1 7 4.5a2.5 2.5 0 0 1 0 5z" fill="var(--yellow)"/></svg>
<div class="info-label" style="top:2978px">Address</div>
<div class="info-line" style="top:3005px">421, Address line goes here<br>45452,Country Name</div>

<svg class="info-icon" style="top:3077px" width="16" height="16" viewBox="0 0 24 24"><path fill="var(--yellow)" d="M6.6 10.8a15 15 0 0 0 6.6 6.6l2.2-2.2c.3-.3.7-.4 1-.2 1.1.4 2.3.6 3.6.6.6 0 1 .4 1 1V20c0 .6-.4 1-1 1A17 17 0 0 1 3 4c0-.6.4-1 1-1h3.5c.6 0 1 .4 1 1 0 1.3.2 2.5.6 3.6.1.3 0 .7-.2 1z"/></svg>
<div class="info-label" style="top:3074px">Phone</div>
<div class="info-line" style="top:3098px;font-weight:600;font-size:17px">044-870 215 364</div>

<svg class="info-icon" style="top:3155px" width="17" height="13" viewBox="0 0 17 13"><rect width="17" height="13" rx="1.5" fill="var(--yellow)"/><path d="M1 1.5l7.5 6 7.5-6" stroke="#fff" stroke-width="1.4" fill="none"/></svg>
<div class="info-label" style="top:3151px">Email</div>
<div class="info-line" style="top:3174px;color:var(--yellow);letter-spacing:.5px">info@dorvikelectricltd.com</div>

<div class="field" style="top:2903px">Name</div>
<div class="field" style="top:2977px">Phone</div>
<div class="field" style="top:3051px">Email</div>
<div class="field" style="top:3126px">Messages</div>
<div class="btn btn-yellow" style="left:554px;top:3212px;width:154px;height:50px">Submit</div>

<footer class="footer"></footer>
<div class="f-mark"></div>
<div class="abs f-name">DORVIK ELECTRIC Ltd</div>
<div class="social" style="left:158px;background:var(--yellow)"></div>
<div class="social" style="left:195px"></div>
<div class="social" style="left:230px"></div>
<div class="social" style="left:267px"></div>

<div class="f-head heading" style="left:406px">Quick Link</div>
<ul class="f-list" style="left:406px">
  <li>Home</li><li>About</li><li>Career</li><li>Events</li><li>Blog</li><li>Contact Us</li>
</ul>
<div class="f-head heading" style="left:596px">Help Link</div>
<ul class="f-list" style="left:596px">
  <li>Terms &amp; Conditions</li><li>Privacy Policy</li><li>About Us</li><li>Support</li>
</ul>
<div class="f-head heading" style="left:809px">Get Our Newsletter</div>
<div class="news-input">Enter Your Email</div>
<div class="btn btn-yellow" style="left:810px;top:3511px;width:277px;height:41px;font-size:14px">Subscribe Now</div>
<div class="f-rule"></div>
<div class="abs copy">©Copyrights 2022&nbsp; Dorvik Electric Ltd |&nbsp;&nbsp; All Rights Reserved</div>

</body>
</html>
```